RTavenor Business Cards & Letterhead

I have a logo but need a design for some new business cards. We are a Design-Build Firm that specializes in the design and construction of commercial projects.
the cards need to be professional. no cartoon stuff.
i would like to have the cards in AI format so I can update the card as needed. Logo is provided.
Our Address is: 4187 Marlowe Ct. Marrowby, North Averland 27614

```html
<!DOCTYPE html>
<html lang="en">
<head>
<meta charset="utf-8">
<title>RTavenor Business Card</title>
<link href="https://fonts.googleapis.com/css2?family=Open+Sans:wght@400;600;700;800&display=swap" rel="stylesheet">
<style>
  :root {
    --stage: #333335;
    --card: #1f1f24;
    --card-back: #1c1c21;
    --edge: #1a7fc9;
    --brand-blue: #1b7ac2;
    --logo-grey: #6e6f73;
    --emboss: #141417;
    --text: #ffffff;
    --panel-a: rgba(44, 62, 82, 0.75);
    --panel-b: rgba(34, 44, 58, 0.35);
  }
  * { box-sizing: border-box; margin: 0; padding: 0; }
  html, body {
    width: 1200px; height: 780px; overflow: hidden;
    background: var(--stage);
    font-family: "Open Sans", Arial, sans-serif;
  }
  .stage {
    width: 1200px; height: 780px;
    display: flex; align-items: center; justify-content: center; gap: 40px;
  }
  .card {
    position: relative;
    width: 540px; height: 309px;
    border-radius: 24px;
    border: 3px solid var(--edge);
    overflow: hidden;
  }
  .card-back { background: var(--card-back); display: flex; align-items: center; justify-content: center; }
  .card-back .wordmark {
    font-size: 58px; font-weight: 800; letter-spacing: 1px;
    color: var(--emboss);
  }
  .card-front { background: var(--card); color: var(--text); }
  .brand {
    position: absolute; left: 28px; top: 30px;
    display: flex; align-items: center; gap: 8px;
  }
  .brand-square { width: 22px; height: 22px; background: var(--brand-blue); }
  .brand-name {
    font-size: 32px; font-weight: 800; color: var(--logo-grey); letter-spacing: 0.5px;
  }
  .accent-panel {
    position: absolute; left: 320px; top: 40px; width: 200px; height: 240px;
    border-radius: 26px;
    background: linear-gradient(160deg, var(--panel-a), var(--panel-b));
  }
  .identity {
    position: absolute; right: 34px; top: 108px; text-align: right;
  }
  .identity .person {
    font-size: 22px; font-weight: 700; color: var(--brand-blue); letter-spacing: 0.5px; line-height: 1.1;
  }
  .identity .role { font-size: 14px; font-weight: 600; color: var(--text); margin-top: 2px; }
  .identity-bar {
    position: absolute; right: 18px; top: 104px; width: 10px; height: 44px;
    background: var(--brand-blue);
  }
  .address {
    position: absolute; left: 34px; top: 150px;
    font-size: 14px; line-height: 1.4; font-weight: 400; font-style: normal;
  }
  .contacts {
    position: absolute; left: 34px; bottom: 24px;
    list-style: none; font-size: 14px; line-height: 1.45;
  }
  .contacts li { display: flex; align-items: center; gap: 8px; }
  .contacts svg { width: 12px; height: 12px; flex: none; }
</style>
</head>
<body>
<main class="stage">
  <section class="card card-back" aria-label="Card back">
    <span class="wordmark">RTAVENOR</span>
  </section>

  <section class="card card-front" aria-label="Card front">
    <div class="accent-panel" aria-hidden="true"></div>

    <div class="brand">
      <span class="brand-square"></span>
      <span class="brand-name">RTAVENOR</span>
    </div>

    <div class="identity-bar"></div>
    <div class="identity">
      <p class="person">RUSSELL TAVENOR</p>
      <p class="role">Founder/President</p>
    </div>

    <address class="address">
      4187 Marlowe Ct. Marrowby,<br>North Averland 27614
    </address>

    <ul class="contacts">
      <li>
        <svg viewBox="0 0 12 12" aria-hidden="true"><path d="M2.5 1h2l1 2.5-1.3 1a6 6 0 0 0 3.3 3.3l1-1.3L11 7.5v2a1 1 0 0 1-1 1A9 9 0 0 1 1.5 2a1 1 0 0 1 1-1z" fill="#1b7ac2"/></svg>
        (919) 555-0148
      </li>
      <li>
        <svg viewBox="0 0 12 12" aria-hidden="true"><circle cx="6" cy="6" r="5" fill="none" stroke="#1b7ac2" stroke-width="1.3"/><path d="M1 6h10M6 1c-2.5 3-2.5 7 0 10M6 1c2.5 3 2.5 7 0 10" fill="none" stroke="#1b7ac2" stroke-width="1"/></svg>
        www.rtavenor.com
      </li>
      <li>
        <svg viewBox="0 0 12 12" aria-hidden="true"><rect x="1" y="2.5" width="10" height="7" rx="1" fill="#1b7ac2"/><path d="M1.5 3l4.5 3.5L10.5 3" fill="none" stroke="#1f1f24" stroke-width="1"/></svg>
        RT@RTavenor.com
      </li>
    </ul>
  </section>
</main>
</body>
</html>
```